Criação de Logo + Papelaria + Manual Básico para Arquitetura
" Somos uma empresa pequena, eu e a minha sócia Débora, atendemos o cliente, fazemos o levantamento de medidas e necessidades do cliente, desenvolvemos o projeto desde o início em 3D colorido, depois o projeto executivo e acompanhamento de obras. Estamos presentes no processo do início ao fim. Buscamos sempre atender o cliente da melhor maneira possível, sempre estando a par de todo o projeto. "

```html
<!DOCTYPE html>
<html lang="pt-BR">
<head>
<meta charset="UTF-8">
<title>Lume Estúdio — Envelopes</title>
<link rel="stylesheet" href="https://fonts.googleapis.com/css2?family=Cormorant+Garamond:wght@500&family=Montserrat:wght@400&display=swap">
<style>
  :root {
    --backdrop: #e8e5e1;
    --envelope-grey: #7d7d7d;
    --flap-grey: #8a8a8a;
    --envelope-white: #ffffff;
    --ink-grey: #6f6f6f;
    --brand-light: #ffffff;
    --shadow: rgba(0, 0, 0, 0.18);
  }
  html, body {
    margin: 0;
    padding: 0;
    overflow: hidden;
  }
  .canvas {
    position: relative;
    width: 1200px;
    height: 1200px;
    background: var(--backdrop);
    overflow: hidden;
  }
  .envelopes {
    position: absolute;
    inset: 0;
  }
  .brand {
    position: absolute;
    margin: 0;
    font-family: "Cormorant Garamond", serif;
    font-weight: 500;
    line-height: 1;
    white-space: nowrap;
  }
  .brand-back {
    left: 221px;
    top: 350px;
    font-size: 58px;
    color: var(--brand-light);
    letter-spacing: 1px;
  }
  .brand-back .brand-sub {
    display: block;
    font-size: 22px;
    letter-spacing: 6px;
    margin-top: 8px;
  }
  .brand-front {
    left: 0;
    width: 1200px;
    top: 812px;
    text-align: center;
    font-size: 40px;
    color: var(--ink-grey);
  }
  .contact {
    position: absolute;
    left: 0;
    width: 1200px;
    margin: 0;
    font-family: "Montserrat", sans-serif;
    font-size: 11.5px;
    color: var(--ink-grey);
    text-align: center;
    display: flex;
    justify-content: center;
    align-items: center;
    gap: 6px;
  }
  .contact-address { top: 881px; }
  .contact-phone { top: 910px; }
  .contact svg { width: 13px; height: 13px; fill: var(--ink-grey); }
</style>
</head>
<body>
<main class="canvas">
  <svg class="envelopes" width="1200" height="1200" viewBox="0 0 1200 1200">
    <defs>
      <filter id="soft-shadow" x="-10%" y="-10%" width="120%" height="130%">
        <feDropShadow dx="0" dy="4" stdDeviation="5" flood-color="#000" flood-opacity="0.2"/>
      </filter>
    </defs>
    <polygon class="envelope-back" filter="url(#soft-shadow)" fill="var(--envelope-grey)"
      points="204,228 840,228 876,269 876,605 168,605 168,269"/>
    <rect class="envelope-front" filter="url(#soft-shadow)" fill="var(--envelope-white)"
      x="324" y="653" width="713" height="302"/>
    <polygon class="envelope-inner-flap" fill="var(--flap-grey)"
      points="324,653 1037,653 1037,660 1000,697 361,697 324,660"/>
  </svg>

  <p class="brand brand-back">Lume<span class="brand-sub">ESTÚDIO</span></p>

  <p class="brand brand-front">Lume</p>

  <p class="contact contact-address">
    <svg viewBox="0 0 24 24" aria-hidden="true"><path d="M12 2a7 7 0 0 0-7 7c0 5.2 7 13 7 13s7-7.8 7-13a7 7 0 0 0-7-7zm0 9.5A2.5 2.5 0 1 1 12 6.5a2.5 2.5 0 0 1 0 5z"/></svg>
    Rua xxxxxxxxxxxxxxxx, nº - Bairro - Cidade - MG | Cep: 00000-000
  </p>
  <p class="contact contact-phone">
    <svg viewBox="0 0 24 24" aria-hidden="true"><path d="M6.6 10.8a15.1 15.1 0 0 0 6.6 6.6l2.2-2.2a1 1 0 0 1 1-.25 11.4 11.4 0 0 0 3.6.57 1 1 0 0 1 1 1V20a1 1 0 0 1-1 1A17 17 0 0 1 3 4a1 1 0 0 1 1-1h3.5a1 1 0 0 1 1 1c0 1.25.2 2.45.57 3.6a1 1 0 0 1-.25 1z"/></svg>
    (00) 0000-0000
  </p>
</main>
</body>
</html>
```